Redesign of luchtvoorraadpunt.nl – Clean, Trustworthy & User-Friendly Medical Equipment We...

PLEASE DO NOT CONTACT US OUTSIDE KRAVELPOINT.COM

We are looking for a talented and creative web designer to redesign the website www.luchtvoorraadpunt.nl, a Dutch online store specializing in medical oxygen concentrators and related products.

The current website is functional but outdated in terms of design, structure, and user experience. We want a fresh, modern, and trustworthy design that reflects the medical and professional nature of the business, while also being clear, accessible, and easy to navigate for a broad audience — including elderly users and people with limited technical skills.

About the Business:
Luchtvoorraadpunt.nl provides high-quality oxygen concentrators and accessories for both home and mobile use. The target audience includes individuals with respiratory conditions, healthcare professionals, and caregivers. Trust, clarity, and ease of use are key.

What We’re Looking For:
A clean and modern layout with a medical/professional feel
Strong focus on usability and accessibility
A design that works flawlessly on desktop and mobile (responsive)
Clear product presentation and easy-to-use navigation
Use of calming colors (e.g. white, light blue, grey tones) that reflect a medical/healthcare environment
Clear call-to-actions (e.g. “Vraag een offerte aan”, “Neem contact op”, etc.)
A design that builds trust and encourages inquiries or purchases

Pages We Need Designed:
Homepage
Product overview page (category)
Product detail page

Inspiration / Style Examples:
We’re looking for something in the style of:

Varnoth Healthcare
Bralto.nl
Welzijnsdepot.nl
Quenby (for clean layout and spacing)

Deliverables:
Full desktop and mobile designs (Figma, Adobe PS)
All source files and assets used (fonts, icons, images, etc.)
Clean and organized layers
Design must be ready for implementation by our development team

Target Market(s)

Luchtvoorraadpunt.nl targets both B2C and B2B audiences within the medical and healthcare sector in europe

Industry/Entity Type

Medical

Number of Pages Required

2 page

Font styles to use
Sans Serif

Requirements
Must have
• Clean and professional design, responsive layout (desktop and mobile), calming medical color scheme (e.g. light blue, white, grey), clear product presentation with specs and images, strong call-to-actions (e.g. "Vraag een offerte aan"), trust elements (certifications, reviews, support info), easy navigation for elderly and non-tech-savvy users, contact form easily accessible, SEO-friendly structure, fast loading design, privacy and regulatory compliance elements (e.g. CE mark info, medical disclaimers).
Should not have
• Overly complex design, dark or aggressive color schemes, small or hard-to-read fonts, cluttered layout, distracting animations, unnecessary pop-ups, autoplay videos or sounds, technical jargon without explanation, hidden contact options, slow-loading pages.

```html
<!DOCTYPE html>
<html lang="en">
<head>
<meta charset="utf-8">
<title>AIRO – Oxygen Concentrators</title>
<link href="https://fonts.googleapis.com/css2?family=Poppins:wght@400;500;600;700&display=swap" rel="stylesheet">
<style>
:root{
  --sky:#8ecdf5;
  --sky-pale:#eaf5fd;
  --sky-btn:#7cc5f2;
  --ink:#2f3237;
  --muted:#5d6168;
  --line:#e6e8eb;
  --red:#e53935;
  --pill:#6b6b6b;
  --brand:#2c5aa0;
  --footer:#3a4759;
  --white:#ffffff;
}
*{box-sizing:border-box;margin:0;padding:0}
html,body{width:1200px;height:3259px;overflow:hidden}
body{font-family:"Poppins",sans-serif;color:var(--ink);background:var(--footer);position:relative}
.abs{position:absolute}
svg{display:block}

/* top bar */
.topbar{position:absolute;top:0;left:0;width:1200px;height:28px;background:var(--white);border-bottom:1px solid var(--line);font-size:10px;color:var(--muted)}
.topbar .links{position:absolute;left:76px;top:8px;display:flex;gap:12px}
.topbar .links-right{position:absolute;right:76px;top:8px;display:flex;gap:12px}
.topbar span{display:flex;align-items:center;gap:4px}

/* header */
.header{position:absolute;top:28px;left:0;width:1200px;height:66px;background:var(--white)}
.logo{position:absolute;left:76px;top:14px;display:flex;align-items:center;gap:8px;font-weight:700;font-size:34px;color:var(--brand);letter-spacing:1px;line-height:1}
.logo i{width:14px;height:14px;border-radius:50%;background:var(--sky-btn);display:block}
.search-toggle{position:absolute;left:350px;top:20px;width:26px;height:26px;border-radius:50%;background:var(--sky-btn)}
.search{position:absolute;left:384px;top:16px;width:316px;height:32px;border:1px solid var(--line);border-radius:16px;font-size:10px;color:#9aa0a6;padding:10px 12px}
.search-btn{position:absolute;left:654px;top:19px;width:46px;height:26px;border-radius:13px;background:var(--pill)}
.lang{position:absolute;left:718px;top:16px;width:98px;height:32px;border:1px solid var(--line);border-radius:16px;font-size:10px;color:#9aa0a6;padding:9px 0 0 35px}
.lang i{position:absolute;left:5px;top:5px;width:22px;height:22px;border-radius:50%;background:var(--sky-btn)}
.header-icons{position:absolute;right:66px;top:20px;display:flex;gap:17px}
.header-icons span{width:25px;height:25px;border-radius:50%;background:#f1f3f5;display:flex;align-items:center;justify-content:center}

/* nav */
.nav{position:absolute;top:94px;left:0;width:1200px;height:55px;background:var(--sky);display:flex;align-items:center;padding-left:160px;font-size:12px;font-weight:600;color:var(--white)}
.nav a{margin-right:36px;text-decoration:none;color:inherit}
.nav a.drop:after{content:"⌄";margin-left:4px;font-size:11px}
.nav .phone{background:var(--pill);border-radius:22px;padding:12px 16px;font-size:12px;font-weight:600}

/* hero */
.hero{position:absolute;top:149px;left:0;width:1200px;height:700px;overflow:hidden}
.hero-photo{position:absolute;inset:0;background:
  radial-gradient(ellipse 260px 320px at 1110px 120px,rgba(236,240,226,.95),rgba(236,240,226,0) 70%),
  radial-gradient(ellipse 230px 300px at 960px 300px,rgba(214,176,122,.9),rgba(214,176,122,0) 70%),
  radial-gradient(ellipse 200px 260px at 760px 260px,rgba(226,186,132,.85),rgba(226,186,132,0) 70%),
  radial-gradient(ellipse 300px 220px at 840px 600px,rgba(96,82,72,.85),rgba(96,82,72,0) 70%),
  radial-gradient(ellipse 260px 200px at 600px 560px,rgba(70,70,76,.7),rgba(70,70,76,0) 70%),
  radial-gradient(ellipse 320px 260px at 560px 330px,rgba(222,214,204,.8),rgba(222,214,204,0) 70%),
  linear-gradient(100deg,#9c9186 0%,#b8aea2 30%,#cfc6ba 55%,#a89a8a 80%,#8e8072 100%)}
.hero-shade{position:absolute;inset:0;background:linear-gradient(90deg,rgba(60,52,46,.45) 0%,rgba(60,52,46,.15) 45%,rgba(0,0,0,0) 70%)}
.hero h1{position:absolute;left:76px;top:240px;font-size:38px;font-weight:700;color:var(--white);line-height:1.1}
.hero .cta{position:absolute;top:351px;height:41px;border-radius:21px;font-size:12px;font-weight:600;display:flex;align-items:center;justify-content:center}
.cta.quote{left:76px;width:174px;background:var(--pill);color:var(--white)}
.cta.contact{left:267px;width:153px;background:var(--white);color:var(--ink)}

/* main white card */
.main{position:absolute;top:805px;left:0;width:1200px;height:2091px;background:var(--white);border-radius:40px;overflow:hidden}
.about-photo{position:absolute;left:148px;top:89px;width:341px;height:341px;border-radius:50%;background:
  radial-gradient(circle at 72% 35%,rgba(244,222,168,.95),rgba(244,222,168,0) 40%),
  radial-gradient(circle at 30% 45%,rgba(120,78,52,.8),rgba(120,78,52,0) 35%),
  radial-gradient(circle at 40% 80%,rgba(214,196,172,.9),rgba(214,196,172,0) 45%),
  linear-gradient(135deg,#b98c5c,#e4c58e 55%,#caa673)}
.about-photo.small{left:347px;top:282px;width:190px;height:190px;border:6px solid var(--white);background:
  radial-gradient(circle at 55% 30%,rgba(190,150,120,.9),rgba(190,150,120,0) 35%),
  radial-gradient(circle at 45% 75%,rgba(92,58,36,.9),rgba(92,58,36,0) 50%),
  linear-gradient(135deg,#cdb79c,#9a7456 55%,#6d4a30)}
.about-text{position:absolute;left:613px;top:148px;width:440px}
h2{font-size:32px;font-weight:600;color:var(--ink);line-height:1.2}
.about-text p,.brand-text p{font-size:12px;line-height:19px;color:var(--muted);margin-top:14px}

.features{position:absolute;left:76px;top:558px;width:1055px;display:flex;gap:14px}
.feature{height:85px;border:1px solid var(--line);border-radius:8px;display:flex;align-items:center;gap:14px;padding:0 18px}
.feature b{display:block;font-size:14px;font-weight:600;color:var(--ink)}
.feature small{font-size:11px;color:var(--muted)}

.gallery{position:absolute;left:0;top:660px;width:1200px;height:396px;background:linear-gradient(to bottom,var(--white) 0%,var(--white) 40%,var(--sky-pale) 100%)}
.gallery h2{position:absolute;width:100%;top:50px;text-align:center}
.gallery .cards{position:absolute;left:143px;top:115px;display:flex;gap:16px}
.gallery .card{width:216px;height:193px;background:var(--white);border:1px solid var(--line);border-radius:8px;overflow:hidden;padding:8px}
.shot{width:100%;height:100%;border-radius:6px}
.tone-white{background:radial-gradient(ellipse 45% 55% at 50% 55%,#cfd6de 0%,#e6eaee 55%,#ffffff 100%)}
.tone-blue{background:radial-gradient(ellipse 42% 55% at 50% 52%,#5f9bd0 0%,#a9cdec 55%,#ffffff 100%)}
.tone-grey{background:radial-gradient(ellipse 42% 55% at 50% 55%,#4a5054 0%,#9aa0a4 55%,#ffffff 100%)}
.tone-black{background:radial-gradient(ellipse 40% 55% at 50% 52%,#1c1e21 0%,#7d8185 55%,#ffffff 100%)}
.tone-valve{background:radial-gradient(ellipse 22% 55% at 50% 50%,#c5ccd2 0%,#e7ebee 55%,#ffffff 100%)}
.tone-mask{background:radial-gradient(ellipse 40% 55% at 50% 50%,#b9ddd2 0%,#dfe6e8 55%,#ffffff 100%)}
.arrow{position:absolute;top:249px;width:33px;height:33px;border-radius:50%;display:flex;align-items:center;justify-content:center}
.arrow.prev{left:91px;background:#5f6368}
.arrow.next{left:1078px;background:var(--sky-btn)}

.bigmark{position:absolute;left:108px;top:1150px;font-size:110px;font-weight:700;color:var(--brand);letter-spacing:4px;line-height:1}
.brand-text{position:absolute;left:521px;top:1125px;width:570px}

.products-head{position:absolute;left:162px;top:1330px;width:875px;height:54px;border-bottom:1px solid var(--line)}
.products-head h2{position:absolute;left:0;top:4px}
.tabs{position:absolute;right:20px;top:18px;display:flex;gap:70px;font-size:14px;color:var(--muted)}
.tabs .on{text-decoration:underline;text-underline-offset:4px}
.products{position:absolute;left:143px;top:1420px;display:flex;gap:16px}
.product{width:216px;height:282px;background:var(--white);border-radius:8px;box-shadow:0 2px 10px rgba(0,0,0,.06);padding:7px}
.product .img{height:152px;border:1px solid var(--line);border-radius:6px;padding:6px}
.product h3{font-size:14px;font-weight:600;line-height:19px;margin:17px 10px 0;height:38px;color:var(--ink)}
.price{margin:14px 10px 0;font-size:11px;font-weight:600;color:var(--red);display:flex;gap:22px;align-items:baseline}
.price.plain{color:var(--muted)}
.price s{color:#9aa0a6;font-weight:400;font-size:9px}
.actions{margin:10px 10px 0}

.shop h2{position:absolute;width:100%;top:1792px;text-align:center}
.shop .sub{position:absolute;width:100%;top:1838px;text-align:center;font-size:14px;color:var(--muted)}
.brands{position:absolute;left:219px;top:1881px;display:flex;gap:9px}
.brand{width:120px;height:120px;border-radius:50%;border:1.5px solid;display:flex;align-items:center;justify-content:center;font-size:13px;font-weight:600;text-align:center}

/* footer */
.footer{position:absolute;left:0;top:2896px;width:1200px;height:363px;color:#e9edf2;font-size:12px}
.footer .logo{left:104px;top:100px;color:var(--white);font-size:44px}
.col{position:absolute;top:55px}
.col h4{font-size:14px;font-weight:600;color:var(--white);margin-bottom:14px}
.col li{list-style:none;line-height:19px}
.col li:before{content:"» "}
.pay{display:flex;gap:6px;margin-top:14px}
.pay span{width:45px;height:30px;border-radius:4px;background:var(--white);color:var(--ink);font-size:7px;font-weight:600;display:flex;align-items:center;justify-content:center}
.copy{position:absolute;width:100%;top:326px;text-align:center;font-size:12px}
.chat{position:absolute;left:1144px;top:286px;width:34px;height:34px;border-radius:50%;background:var(--white);display:flex;align-items:center;justify-content:center}
</style>
</head>
<body>

<div class="topbar">
  <div class="links">
    <span><svg width="10" height="10" viewBox="0 0 10 10"><path d="M1 5L5 1l4 4v4H1z" fill="none" stroke="#5d6168"/></svg>Home</span>
    <span><svg width="10" height="10" viewBox="0 0 10 10"><circle cx="5" cy="3" r="2" fill="none" stroke="#5d6168"/><path d="M1 9c0-2 2-3 4-3s4 1 4 3" fill="none" stroke="#5d6168"/></svg>About Us</span>
    <span><svg width="10" height="10" viewBox="0 0 10 10"><rect x="1" y="2" width="8" height="6" fill="none" stroke="#5d6168"/><path d="M1 2l4 3 4-3" fill="none" stroke="#5d6168"/></svg>Contact</span>
  </div>
  <div class="links-right">
    <span><svg width="12" height="10" viewBox="0 0 12 10"><rect x="0" y="2" width="7" height="5" fill="#5d6168"/><rect x="7" y="4" width="4" height="3" fill="#5d6168"/><circle cx="3" cy="8" r="1.5" fill="#5d6168"/><circle cx="9" cy="8" r="1.5" fill="#5d6168"/></svg>Delivery</span>
    <span><svg width="10" height="10" viewBox="0 0 10 10"><path d="M5 1l4 2v4L5 9 1 7V3z" fill="none" stroke="#5d6168"/></svg>Stock</span>
  </div>
</div>

<header class="header">
  <div class="logo"><i></i>AIRO</div>
  <div class="search-toggle"><svg width="26" height="26" viewBox="0 0 26 26"><path d="M10 11l3 3 3-3" fill="none" stroke="#fff" stroke-width="1.5"/></svg></div>
  <div class="search">Search Here...</div>
  <div class="search-btn"><svg width="46" height="26" viewBox="0 0 46 26"><circle cx="22" cy="12" r="4" fill="none" stroke="#fff" stroke-width="1.5"/><path d="M25 15l3 3" stroke="#fff" stroke-width="1.5"/></svg></div>
  <div class="lang"><i></i>English</div>
  <div class="header-icons">
    <span><svg width="12" height="12" viewBox="0 0 12 12"><circle cx="6" cy="3.5" r="2.5"/><path d="M1 12c0-3 2.5-5 5-5s5 2 5 5z"/></svg></span>
    <span><svg width="12" height="12" viewBox="0 0 12 12"><path d="M1 4h9M7 1l3 3-3 3M11 8H2M5 5L2 8l3 3" fill="none" stroke="#000" stroke-width="1.3"/></svg></span>
    <span><svg width="12" height="12" viewBox="0 0 12 12"><rect x="2" y="1" width="8" height="10" rx="1"/></svg></span>
    <span><svg width="12" height="12" viewBox="0 0 12 12"><path d="M0 1h2l2 7h6l1-5H3"/><circle cx="5" cy="10.5" r="1"/><circle cx="9" cy="10.5" r="1"/></svg></span>
    <span><svg width="12" height="12" viewBox="0 0 12 12"><path d="M6 11L1 6a3 3 0 015-4 3 3 0 015 4z"/></svg></span>
  </div>
</header>

<nav class="nav">
  <a class="drop">All categories</a>
  <a class="drop">Oxygen concentrator</a>
  <a class="drop">Portable Oxygen concentrator</a>
  <a>Filters</a>
  <a>Rental</a>
  <a>Supplies</a>
  <span class="phone">0031-705550123</span>
</nav>

<section class="hero">
  <div class="hero-photo" role="img" aria-label="Photo of a mother using an oxygen mask on a sofa beside her daughter holding a tablet, in a bright living room"></div>
  <div class="hero-shade"></div>
  <h1>Your trusted partner&nbsp; with<br>Oxygen Concentrators.</h1>
  <span class="cta quote">Vraag een offerte aan</span>
  <span class="cta contact">Neem contact op</span>
</section>

<main class="main">
  <div class="about-photo" role="img" aria-label="Photo of a woman helping a girl with an oxygen mask"></div>
  <div class="about-photo small" role="img" aria-label="Photo of a man using a nasal oxygen cannula with a tablet"></div>
  <div class="about-text">
    <h2>About Airo Us</h2>
    <p>As business and consumer you want the best equipment for the sharpest prices. We offer the best stationary oxygen concentrators, portable oxygen concentrators, accessories and disposables. Compare and make the best choice for you and your business.</p>
    <p>AIRO BV more than 22 years experience your partner for innovative technology and service. With our online shop&nbsp; we keep&nbsp; you constantly informed of the various systems. Questons or wishes? don't hesitate to contact us.</p>
  </div>

  <div class="features">
    <div class="feature" style="width:232px">
      <svg width="48" height="30" viewBox="0 0 48 30"><rect x="2" y="4" width="28" height="18" rx="2" fill="#8ecdf5"/><path d="M30 9h9l6 7v6H30z" fill="#8ecdf5"/><circle cx="11" cy="24" r="4" fill="#fff" stroke="#8ecdf5" stroke-width="2"/><circle cx="38" cy="24" r="4" fill="#fff" stroke="#8ecdf5" stroke-width="2"/></svg>
      <div><b>Free Shipping</b><small>above € 250 in the EU</small></div>
    </div>
    <div class="feature" style="width:284px">
      <svg width="46" height="40" viewBox="0 0 46 40"><path d="M23 38L4 20A11 11 0 0123 7a11 11 0 0119 13z" fill="#8ecdf5"/></svg>
      <div><b>Oxygen concentrator</b><small>Oxygen concentrator for travel</small></div>
    </div>
    <div class="feature" style="width:247px">
      <svg width="52" height="40" viewBox="0 0 52 40"><rect x="2" y="4" width="34" height="24" rx="3" fill="#8ecdf5"/><rect x="2" y="9" width="34" height="5" fill="#5aaee4"/><rect x="36" y="22" width="14" height="14" rx="2" fill="#8ecdf5"/><path d="M39 22v-4a4 4 0 018 0v4" fill="none" stroke="#8ecdf5" stroke-width="2.5"/></svg>
      <div><b>Secure Shopping</b><small>Best security features</small></div>
    </div>
    <div class="feature" style="width:248px">
      <svg width="44" height="40" viewBox="0 0 44 40"><circle cx="22" cy="9" r="6" fill="#8ecdf5"/><circle cx="9" cy="13" r="5" fill="#8ecdf5"/><circle cx="35" cy="13" r="5" fill="#8ecdf5"/><path d="M12 38c0-9 5-14 10-14s10 5 10 14z" fill="#8ecdf5"/><path d="M1 36c0-8 4-12 8-12s6 3 6 5v7zM43 36c0-8-4-12-8-12s-6 3-6 5v7z" fill="#8ecdf5"/></svg>
      <div><b>22 years experience</b><small>Best security features</small></div>
    </div>
  </div>

  <section class="gallery">
    <h2>Gallery Home Oxygen</h2>
    <span class="arrow prev"><svg width="10" height="10" viewBox="0 0 10 10"><path d="M6 2L3 5l3 3" fill="none" stroke="#fff" stroke-width="1.5"/></svg></span>
    <div class="cards">
      <div class="card"><div class="shot tone-white" role="img" aria-label="Product photo of a white and grey portable oxygen concentrator"></div></div>
      <div class="card"><div class="shot tone-blue" role="img" aria-label="Product photo of a light blue stationary oxygen concentrator"></div></div>
      <div class="card"><div class="shot tone-grey" role="img" aria-label="Product photo of a dark grey oxygen concentrator on wheels"></div></div>
      <div class="card"><div class="shot tone-black" role="img" aria-label="Product photo of a black stationary oxygen concentrator"></div></div>
    </div>
    <span class="arrow next"><svg width="10" height="10" viewBox="0 0 10 10"><path d="M4 2l3 3-3 3" fill="none" stroke="#fff" stroke-width="1.5"/></svg></span>
  </section>

  <div class="bigmark">AIRO</div>
  <div class="brand-text">
    <h2>AIRO BV Oxygen concentrator</h2>
    <p>AIRO BV was founded in 2003 and has a premium range of oxygen concentrators. We have the largest online offers for the Netherlands and Belgium.Whether you are looking for a fixed oxygen concentrator or a portable / portable / mobile oxygen concentrator. We make the difference in knowledge, service and low prices.</p>
  </div>

  <div class="products-head">
    <h2>Products</h2>
    <div class="tabs"><span>Recently Viewed</span><span class="on">Most Viewed</span></div>
  </div>
  <div class="products">
    <div class="product">
      <div class="img"><div class="shot tone-blue" role="img" aria-label="Product photo of a light blue stationary oxygen concentrator"></div></div>
      <h3>Calvero Restflow oxygen...</h3>
      <div class="price">€790.25 <s>€900.00</s></div>
      <div class="actions"><svg width="60" height="12" viewBox="0 0 60 12" fill="none" stroke="#8a9097"><path d="M6 11L1 6a2.8 2.8 0 015-3.5A2.8 2.8 0 0111 6z"/><path d="M22 2h2l1.5 6h5l1-4h-6.5"/><path d="M43 3h2l5 6h2M43 9h2l5-6h2"/></svg></div>
    </div>
    <div class="product">
      <div class="img"><div class="shot tone-valve" role="img" aria-label="Product photo of a transparent fire safety valve for oxygen tubing"></div></div>
      <h3>Firesafe valve</h3>
      <div class="price plain">€9.95</div>
      <div class="actions"><svg width="60" height="12" viewBox="0 0 60 12" fill="none" stroke="#8a9097"><path d="M6 11L1 6a2.8 2.8 0 015-3.5A2.8 2.8 0 0111 6z"/><path d="M22 2h2l1.5 6h5l1-4h-6.5"/><path d="M43 3h2l5 6h2M43 9h2l5-6h2"/></svg></div>
    </div>
    <div class="product">
      <div class="img"><div class="shot tone-black" role="img" aria-label="Product photo of a black compact oxygen concentrator"></div></div>
      <h3>Oxygen concentrator Compact 410PX</h3>
      <div class="price">€801.15 <s>€899.25</s></div>
      <div class="actions"><svg width="60" height="12" viewBox="0 0 60 12" fill="none" stroke="#8a9097"><path d="M6 11L1 6a2.8 2.8 0 015-3.5A2.8 2.8 0 0111 6z"/><path d="M22 2h2l1.5 6h5l1-4h-6.5"/><path d="M43 3h2l5 6h2M43 9h2l5-6h2"/></svg></div>
    </div>
    <div class="product">
      <div class="img"><div class="shot tone-mask" role="img" aria-label="Product photo of an oxygen mask with green tubing on a display bust"></div></div>
      <h3>Oxygen Mask with 2.1 meter hose</h3>
      <div class="price">€2.18 <s>€2.73</s></div>
      <div class="actions"><svg width="60" height="12" viewBox="0 0 60 12" fill="none" stroke="#8a9097"><path d="M6 11L1 6a2.8 2.8 0 015-3.5A2.8 2.8 0 0111 6z"/><path d="M22 2h2l1.5 6h5l1-4h-6.5"/><path d="M43 3h2l5 6h2M43 9h2l5-6h2"/></svg></div>
    </div>
  </div>

  <section class="shop">
    <h2>Shop by Brand</h2>
    <div class="sub">All Manufacturers</div>
    <div class="brands">
      <div class="brand" style="border-color:#2f3237;color:#2f3237">Dunmere<br>Strade</div>
      <div class="brand" style="border-color:#2c7fc2;color:#2c7fc2">Aeron<br>Concepts</div>
      <div class="brand" style="border-color:#2c7fc2;color:#2c7fc2">Velora</div>
      <div class="brand" style="border-color:#1f9a55;color:#1f9a55">Brindle Labs</div>
      <div class="brand" style="border-color:#2b3fc2;color:#2b3fc2">Ostrava Care</div>
      <div class="brand" style="border-color:#e53935;color:#e53935">Halvex</div>
    </div>
  </section>
</main>

<footer class="footer">
  <div class="logo"><i></i>AIRO</div>
  <div class="col" style="left:358px">
    <h4>Useful Links</h4>
    <ul><li>Home</li><li>About</li><li>All categories</li><li>Oxygen concentrator</li><li>Portable Oxygen concentrator</li><li>Filters</li><li>Rental</li><li>Supplies</li><li>Contact</li></ul>
  </div>
  <div class="col" style="left:625px">
    <h4>Customer Service</h4>
    <ul><li>Contact</li><li>Warranty and Service</li><li>Returns</li><li>Site Map</li><li>Brands</li></ul>
    <h4 style="margin:16px 0 6px 8px">My Account</h4>
    <ul><li>My Account</li><li>Order History</li></ul>
  </div>
  <div class="col" style="left:846px">
    <h4>Documentation</h4>
    <ul><li>Frequently asked questions</li></ul>
    <h4 style="margin-top:36px;margin-bottom:0">Payments</h4>
    <div class="pay"><span>Paywick</span><span>Vantix</span><span>Meridian</span><span>Dorvane</span><span>Alder Exp.</span></div>
  </div>
  <div class="copy">Copyright © 2003-2025, AIRO BV, All Rights Reserved</div>
  <div class="chat"><svg width="20" height="18" viewBox="0 0 20 18"><path d="M10 1C5 1 1 4 1 8c0 2 1 4 3 5l-1 4 4-3c1 .3 2 .3 3 .3 5 0 9-3 9-7s-4-7-9-7z" fill="#3a4759"/><circle cx="6" cy="8" r="1.2" fill="#fff"/><circle cx="10" cy="8" r="1.2" fill="#fff"/><circle cx="14" cy="8" r="1.2" fill="#fff"/></svg></div>
</footer>

</body>
</html>
```